Help me make landing pages for my web application that are mobile friendly

I need to make 2 mobile friendly landing pages for an application. The 2 pages will be related. First I need a home page and then I need a working page. I do not want to change the color scheme or logos. Just layout and design.

```html
<!DOCTYPE html>
<html lang="en">
<head>
<meta charset="utf-8">
<title>ShiftCover – Mobile Screens</title>
<link href="https://fonts.googleapis.com/css2?family=Mulish:wght@400;500;600;700&display=swap" rel="stylesheet">
<style>
:root{
  --purple:#6b52a3;
  --purple-dark:#5b4391;
  --surface:#f3f5fb;
  --card:#ffffff;
  --teal:#2aa6cc;
  --sky:#3db9ef;
  --green:#0c8a14;
  --red:#e0123c;
  --ink:#1d1d24;
  --muted:#5d5d68;
  --field:#f1f2f7;
}
*{box-sizing:border-box;margin:0;padding:0}
html,body{width:952px;height:1200px;overflow:hidden;background:#fff;font-family:"Mulish",sans-serif;color:var(--ink)}
.stage{position:absolute;left:0;top:0;width:1377px;height:1737px;transform:scale(.6914);transform-origin:0 0}
.phone{position:absolute;top:36px;width:414px;height:1527px;background:var(--purple);border-radius:50px 50px 40px 40px;overflow:hidden}
.phone.detail{height:1654px;border-radius:50px 50px 50px 50px}
.menu-btn{position:absolute;left:20px;top:44px}
.brand{position:absolute;left:116px;top:34px;display:flex;align-items:center;gap:10px;color:#fff;font-size:28px;font-weight:600}
.brand .mark{width:28px;height:28px;border-radius:50%;background:var(--teal)}
.body{position:absolute;left:0;right:0;top:99px;bottom:0;background:var(--surface);border-radius:40px}
.detail .body{top:106px;bottom:50px;border-radius:40px 40px 50px 50px}
.tabs{position:absolute;left:20px;top:136px;display:flex;gap:10px;white-space:nowrap}
.tab{height:30px;padding:0 22px;border-radius:15px;background:#fff;font-size:12px;line-height:30px;box-shadow:0 2px 6px rgba(0,0,0,.05)}
.tab.on{background:linear-gradient(90deg,#47c2f3,#2b9fe0);color:#fff}
.panel{position:absolute;left:20px;top:192px;width:374px;height:1282px;background:var(--purple);border-radius:20px}
.job{position:absolute;left:36px;width:339px;height:182px;background:var(--card);border-radius:18px}
.job .for{position:absolute;left:19px;top:22px;font-size:16px}
.job .st{position:absolute;left:163px;top:19px;font-size:16px}
.badge{position:absolute;left:230px;top:14px;width:91px;height:31px;border-radius:16px;color:#fff;font-size:12px;text-align:center;line-height:31px}
.b-done{background:linear-gradient(90deg,#47c2f3,#2b9fe0)}
.b-act{background:var(--green)}
.b-cxl{background:var(--red)}
.avatar{position:absolute;left:18px;top:58px;width:46px;height:46px;border-radius:50%;background:radial-gradient(circle at 50% 40%,#e9c3a4,#8b6a55)}
.who{position:absolute;left:75px;top:64px;font-size:12px;line-height:18px}
.who b{display:block;font-weight:500;color:var(--teal)}
.who span{color:var(--muted)}
.meta{position:absolute;left:19px;font-size:12px}
.drawer{position:absolute;left:29px;top:69px;width:236px;height:543px;background:#fff;border-radius:20px;box-shadow:0 10px 30px rgba(40,20,80,.25)}
.drawer .dbrand{position:absolute;left:22px;top:36px;display:flex;align-items:center;gap:8px;color:var(--purple);font-size:26px;font-weight:600}
.drawer .dbrand .mark{width:26px;height:26px;border-radius:50%;background:var(--teal)}
.drawer .pic{position:absolute;left:23px;top:95px;width:62px;height:62px;border-radius:50%;background:radial-gradient(circle at 50% 40%,#f0cba8,#7a4e2e)}
.drawer .uname{position:absolute;left:23px;top:174px;font-size:19px;font-weight:600;color:var(--teal)}
.drawer .mail{position:absolute;left:23px;top:204px;font-size:14px}
.nav{position:absolute;left:23px;top:259px;list-style:none}
.nav li{display:flex;align-items:center;gap:12px;height:40px;margin-bottom:15px;padding-left:18px;font-size:15px}
.nav li.on{width:112px;background:var(--purple);color:#fff;border-radius:20px}
.sec{position:absolute;left:20px;width:374px;background:#fff;border-radius:20px}
.sec h2{position:absolute;left:24px;top:26px;font-size:17px;font-weight:600;color:var(--teal)}
.row{position:absolute;left:25px;font-size:12px}
.row b{font-weight:700}
.field{position:absolute;left:24px;width:320px;background:var(--field);border-radius:8px;font-size:12px;color:var(--muted);padding:12px 14px;line-height:16px}
.pill{position:absolute;height:30px;padding:0 18px;border-radius:15px;background:var(--purple);color:#fff;font-size:12px;display:flex;align-items:center;gap:6px}
.dot{position:absolute;right:12px;top:12px;width:14px;height:14px;border-radius:50%;background:var(--purple)}
</style>
</head>
<body>
<div class="stage">

<!-- Screen 1: assignments -->
<section class="phone" style="left:34px">
  <svg class="menu-btn" width="24" width="24" height="20" viewBox="0 0 24 20"><g stroke="#fff" stroke-width="2.2" stroke-linecap="round"><line x1="2" y1="3" x2="20" y2="3"/><line x1="2" y1="10" x2="14" y2="10"/><line x1="2" y1="17" x2="20" y2="17"/></g></svg>
  <div class="brand"><span class="mark"></span>ShiftCover</div>
  <div class="body"></div>
  <nav class="tabs"><span class="tab on">My Assigments</span><span class="tab">Available Openings</span><span class="tab">My Assignments</span></nav>
  <div class="panel"></div>

  <article class="job" style="top:227px"><span class="for">Sibbing For :</span><span class="st">Status :</span><span class="badge b-done">Complete</span><div class="avatar" role="img" aria-label="Teacher portrait photo"></div><div class="who"><b>Nora Ellison</b><span>Teacher</span></div><span class="meta" style="top:117px">Location : DVES</span><span class="meta" style="top:142px">Time Slots : 09/02 - 09/02 (1h 0m)</span></article>
  <article class="job" style="top:433px"><span class="for">Sibbing For :</span><span class="st">Status :</span><span class="badge b-done">Complete</span><div class="avatar" role="img" aria-label="Teacher portrait photo"></div><div class="who"><b>Extra Duty</b><span>Teacher</span></div><span class="meta" style="top:117px">Location : DVES</span><span class="meta" style="top:142px">Time Slots : 07/12 - 07/11 (1h 20m)</span></article>
  <article class="job" style="top:638px"><span class="for">Sibbing For :</span><span class="st">Status :</span><span class="badge b-done">Complete</span><div class="avatar" role="img" aria-label="Teacher portrait photo"></div><div class="who"><b>Owen Hartley</b><span>Teacher</span></div><span class="meta" style="top:117px">Location : DVES</span><span class="meta" style="top:142px">Time Slots : 09/02 - 09/02 (1h 0m)</span></article>
  <article class="job" style="top:844px"><span class="for">Sibbing For :</span><span class="st">Status :</span><span class="badge b-act">Active</span><div class="avatar" role="img" aria-label="Teacher portrait photo"></div><div class="who"><b>Grace Whitfield</b><span>Teacher</span></div><span class="meta" style="top:117px">Location : DVES</span><span class="meta" style="top:142px">Time Slots : &nbsp;07/26 - 08/07 (14h 15m)</span></article>
  <article class="job" style="top:1049px"><span class="for">Sibbing For :</span><span class="st">Status :</span><span class="badge b-cxl">Canceled</span><div class="avatar" role="img" aria-label="Teacher portrait photo"></div><div class="who"><b>Priya Lanford</b><span>Teacher</span></div><span class="meta" style="top:117px">Location : DVES</span><span class="meta" style="top:142px">Time Slots : 01/31 - 07/31 (9h 0m)</span></article>
  <article class="job" style="top:1255px"><span class="for">Sibbing For :</span><span class="st">Status :</span><span class="badge b-act">Active</span><div class="avatar" role="img" aria-label="Teacher portrait photo"></div><div class="who"><b>Marcus Delaney</b><span>Teacher</span></div><span class="meta" style="top:117px">Location : DVES</span><span class="meta" style="top:142px">Time Slots : 09/02 - 09/02 (1h 0m)</span></article>
</section>

<!-- Screen 2: menu open -->
<section class="phone" style="left:474px">
  <svg class="menu-btn" width="24" height="20" viewBox="0 0 24 20"><g stroke="#fff" stroke-width="2.2" stroke-linecap="round"><line x1="2" y1="3" x2="20" y2="3"/><line x1="2" y1="10" x2="14" y2="10"/><line x1="2" y1="17" x2="20" y2="17"/></g></svg>
  <div class="brand"><span class="mark"></span>ShiftCover</div>
  <div class="body"></div>
  <nav class="tabs"><span class="tab on">My Assigments</span><span class="tab">Available Openings</span><span class="tab">My Assignments</span></nav>
  <div class="panel"></div>

  <article class="job" style="top:227px"><span class="for">Sibbing For :</span><span class="st">Status :</span><span class="badge b-done">Complete</span></article>
  <article class="job" style="top:433px"><span class="for">Sibbing For :</span><span class="st">Status :</span><span class="badge b-done">Complete</span></article>
  <article class="job" style="top:638px"><span class="for">Sibbing For :</span><span class="st">Status :</span><span class="badge b-done">Complete</span><div class="avatar" role="img" aria-label="Teacher portrait photo"></div><div class="who"><b>Owen Hartley</b><span>Teacher</span></div><span class="meta" style="top:117px">Location : DVES</span><span class="meta" style="top:142px">Time Slots : 09/02 - 09/02 (1h 0m)</span></article>
  <article class="job" style="top:844px"><span class="for">Sibbing For :</span><span class="st">Status :</span><span class="badge b-act">Active</span><div class="avatar" role="img" aria-label="Teacher portrait photo"></div><div class="who"><b>Grace Whitfield</b><span>Teacher</span></div><span class="meta" style="top:117px">Location : DVES</span><span class="meta" style="top:142px">Time Slots : &nbsp;07/26 - 08/07 (14h 15m)</span></article>
  <article class="job" style="top:1049px"><span class="for">Sibbing For :</span><span class="st">Status :</span><span class="badge b-cxl">Canceled</span><div class="avatar" role="img" aria-label="Teacher portrait photo"></div><div class="who"><b>Priya Lanford</b><span>Teacher</span></div><span class="meta" style="top:117px">Location : DVES</span><span class="meta" style="top:142px">Time Slots : 01/31 - 07/31 (9h 0m)</span></article>
  <article class="job" style="top:1255px"><span class="for">Sibbing For :</span><span class="st">Status :</span><span class="badge b-act">Active</span><div class="avatar" role="img" aria-label="Teacher portrait photo"></div><div class="who"><b>Marcus Delaney</b><span>Teacher</span></div><span class="meta" style="top:117px">Location : DVES</span><span class="meta" style="top:142px">Time Slots : 09/02 - 09/02 (1h 0m)</span></article>

  <aside class="drawer">
    <div class="dbrand"><span class="mark"></span>ShiftCover</div>
    <div class="pic" role="img" aria-label="User profile photo"></div>
    <div class="uname">Rosalie</div>
    <div class="mail">r.cover.2@mailbox.test</div>
    <ul class="nav">
      <li class="on"><svg width="18" height="16" viewBox="0 0 18 16"><path d="M9 1 1 8h2.5v7h4v-4h3v4h4V8H17z" fill="#fff"/></svg>Home</li>
      <li><svg width="16" height="16" viewBox="0 0 16 16"><rect x="1" y="3" width="14" height="12" rx="1.5" fill="#222"/><path d="M4.5 9.5 7 12l4.5-4.5" stroke="#fff" stroke-width="1.6" fill="none"/><rect x="4" y="1" width="2" height="4" fill="#222"/><rect x="10" y="1" width="2" height="4" fill="#222"/></svg>Available Opening</li>
      <li><svg width="16" height="18" viewBox="0 0 16 18"><rect x="2" y="2" width="12" height="15" rx="1.5" fill="#222"/><rect x="5" y="1" width="6" height="3" fill="#fff" stroke="#222"/><g stroke="#fff" stroke-width="1.4"><line x1="5" y1="8" x2="11" y2="8"/><line x1="5" y1="11" x2="11" y2="11"/><line x1="5" y1="14" x2="9" y2="14"/></g></svg>Assignments</li>
      <li><svg width="16" height="18" viewBox="0 0 16 18"><circle cx="8" cy="6" r="5" fill="#222"/><path d="M1 17c0-4 3-6 7-6s7 2 7 6z" fill="#222"/></svg>Support</li>
      <li><svg width="16" height="16" viewBox="0 0 16 16"><path d="M5 3.5a6 6 0 1 0 6 0" stroke="#222" stroke-width="2.2" fill="none" stroke-linecap="round"/><line x1="8" y1="1" x2="8" y2="8" stroke="#222" stroke-width="2.2" stroke-linecap="round"/></svg>Logout</li>
    </ul>
  </aside>
</section>

<!-- Screen 3: opening detail -->
<section class="phone detail" style="left:929px">
  <svg class="menu-btn" width="24" height="20" viewBox="0 0 24 20"><g stroke="#fff" stroke-width="2.2" stroke-linecap="round"><line x1="2" y1="3" x2="20" y2="3"/><line x1="2" y1="10" x2="14" y2="10"/><line x1="2" y1="17" x2="20" y2="17"/></g></svg>
  <div class="brand"><span class="mark"></span>ShiftCover</div>
  <div class="body"></div>

  <div class="sec" style="top:145px;height:331px">
    <h2>Opening information</h2>
    <p class="row" style="top:62px"><b>Summary :</b> Testing - Test</p>
    <p class="row" style="top:95px"><b>Location :</b> Maple Ridge Elementary School</p>
    <p class="row" style="top:128px"><b>Type :</b> Vacancy</p>
    <p class="row" style="top:161px"><b>Regular Staff :</b> Owen Hartley</p>
    <p class="row" style="top:195px"><b>Department :</b></p>
    <div class="field" style="top:225px;height:75px;color:var(--ink)">asdg<br>sdfg</div>
  </div>

  <div class="sec" style="top:504px;height:288px">
    <h2>Comments</h2>
    <div class="field" style="top:68px;height:76px">Write a comment or upload a file...</div>
    <span class="pill" style="left:24px;top:162px"><svg width="14" height="12" viewBox="0 0 14 12"><path d="M1 6 13 1 10 11 7 7z" fill="#fff"/></svg>Post</span>
    <span class="pill" style="left:126px;top:162px"><svg width="11" height="12" viewBox="0 0 11 12"><rect x="1" y="1" width="9" height="10" rx="1.5" fill="none" stroke="#fff" stroke-width="1.6"/></svg>Upload</span>
    <div class="field" style="top:212px;height:37px;padding-top:11px">No Comments or files uploaded</div>
  </div>

  <div class="sec" style="top:823px;height:172px">
    <h2>Additional Details</h2>
    <p class="row" style="top:71px;font-weight:600">Parking Spot</p>
    <div class="field" style="top:99px;height:37px"></div>
  </div>

  <div class="sec" style="top:1034px;height:462px">
    <h2>Time Slots</h2>
    <span class="pill" style="left:20px;top:74px"><svg width="13" height="13" viewBox="0 0 13 13"><circle cx="6.5" cy="6.5" r="6" fill="#fff"/><path d="M3.5 6.5 5.8 8.8 9.5 4.8" stroke="#6b52a3" stroke-width="1.6" fill="none"/></svg>Accept</span>
    <span class="pill" style="left:122px;top:74px"><svg width="11" height="12" viewBox="0 0 11 12"><rect x="1" y="1" width="9" height="10" rx="1.5" fill="none" stroke="#fff" stroke-width="1.6"/></svg>Withdraw</span>
    <p class="row" style="top:134px;left:23px;font-weight:600">Date :</p>
    <div class="field" style="top:150px;left:21px;height:37px;color:var(--ink)">3/19/2026<span class="dot" style="border-radius:2px"></span></div>
    <p class="row" style="top:212px;left:23px;font-weight:600">From :</p>
    <div class="field" style="top:229px;left:21px;height:37px;color:var(--ink)">9.30 AM<span class="dot"></span></div>
    <p class="row" style="top:291px;left:23px;font-weight:600">To :</p>
    <div class="field" style="top:308px;left:21px;height:37px;color:var(--ink)">12.30 AM<span class="dot"></span></div>
    <p class="row" style="top:375px;left:23px"><b>Current Assignment :</b> No Assignment</p>
    <p class="row" style="top:408px;left:23px"><b>Status :</b> Active</p>
  </div>

  <span class="pill" style="left:110px;top:1530px;padding:0 24px"><svg width="13" height="13" viewBox="0 0 13 13"><rect x="1" y="1" width="11" height="11" rx="1.5" fill="#fff"/><rect x="3.5" y="2" width="6" height="3" fill="#6b52a3"/></svg>Save</span>
  <span class="pill" style="left:212px;top:1530px;padding:0 20px"><svg width="13" height="13" viewBox="0 0 13 13"><circle cx="6.5" cy="6.5" r="6" fill="#fff"/><path d="M4.3 4.3 8.7 8.7M8.7 4.3 4.3 8.7" stroke="#6b52a3" stroke-width="1.6"/></svg>Close</span>
</section>

</div>
</body>
</html>
```